Property management company looking for modern card design

We at Blue Heron Partners provides property management services for its residential and commercial properties, with expertise in all categories of multifamily, industrial and office projects throughout California.

We need a business card design that is professional and modern designed business card. In our field, clients get hundreds of business cards, we would like our card to stand out.

Please avoid small print.

Target Market(s)

Professionals and high end clients

Industry/Entity Type

Financial Planning

Contact Information for Business Card

Company Name: Blue Heron Partners, Name, email, license #, phone number, website blueheronpartners.com

Font styles to use
Sans Serif

Requirements
Must have
• The card design needs to be adaptable because there is a possibly we will be expanding into different sectors other than real estate. The card design should be focused on financial planning and asset management.
Nice to have
• Modern and simple business card. Eye catching. Non-standard size/shaped cards would be great.
• blueheronpartners.com
Should not have
• Too many bright color or any pictures or shapes of real estate stuff.

```html
<!DOCTYPE html>
<html lang="en">
<head>
<meta charset="utf-8">
<title>Blue Heron Partners – Business Card</title>
<link href="https://fonts.googleapis.com/css2?family=Open+Sans:wght@400;600&display=swap" rel="stylesheet">
<style>
  :root {
    --backdrop: #869a97;
    --card: #050707;
    --red: #e8101d;
    --red-deep: #b80d18;
    --muted: #9a9e9e;
  }
  * { margin: 0; padding: 0; box-sizing: border-box; }
  html, body {
    width: 1200px; height: 1200px; overflow: hidden;
    background: var(--backdrop);
    font-family: "Open Sans", sans-serif;
  }
  .canvas { position: relative; width: 1200px; height: 1200px; }
  .card {
    position: absolute; width: 668px; height: 382px;
    background: var(--card);
  }
  .card--front { left: 246px; top: 146px; }
  .card--back { left: 244px; top: 636px; }

  .brand-mark {
    position: absolute; border-radius: 50%;
    background: var(--red-deep);
  }
  .card--front .brand-mark { width: 124px; height: 124px; left: 272px; top: 97px; }
  .card--back .brand-mark { width: 102px; height: 102px; left: 123px; top: 119px; }

  .brand-name {
    position: absolute; left: 0; width: 100%;
    text-align: center; color: var(--red);
    font-weight: 600; text-transform: uppercase; white-space: nowrap;
  }
  .card--front .brand-name { top: 240px; font-size: 28px; letter-spacing: 0.12em; }
  .card--back .brand-name { top: 228px; width: 335px; font-size: 19px; letter-spacing: 0.1em; }

  .divider {
    position: absolute; left: 335px; top: 112px;
    width: 2px; height: 188px; background: var(--red-deep);
  }
  .holder { position: absolute; left: 430px; top: 70px; color: var(--red); line-height: 1.05; }
  .holder__name { font-size: 28px; }
  .holder__role { font-size: 20px; }

  .contact { list-style: none; }
  .contact__item { position: absolute; left: 0; width: 668px; height: 30px; }
  .contact__icon { position: absolute; left: 372px; top: 0; width: 28px; height: 28px; }
  .contact__text { position: absolute; left: 480px; top: 2px; color: var(--muted); font-size: 20px; }
  .contact__item--phone .contact__text { font-size: 25px; top: -6px; left: 482px; }
</style>
</head>
<body>
<div class="canvas">
  <section class="card card--front">
    <span class="brand-mark"></span>
    <p class="brand-name">Blue Heron Partners</p>
  </section>

  <section class="card card--back">
    <span class="brand-mark"></span>
    <p class="brand-name">Blue Heron Partners</p>
    <span class="divider"></span>
    <div class="holder">
      <p class="holder__name">Name</p>
      <p class="holder__role">position</p>
    </div>
    <ul class="contact">
      <li class="contact__item contact__item--phone" style="top:180px">
        <svg class="contact__icon" viewBox="0 0 24 24"><path fill="#e8101d" d="M6.6 3.5l2.6 3.2-1.6 2.1c1.1 2.6 3 4.5 5.6 5.6l2.1-1.6 3.2 2.6-1.4 3.1C10.4 18.3 5.7 13.6 3.5 6.9z"/></svg>
        <span class="contact__text">phone</span>
      </li>
      <li class="contact__item" style="top:228px">
        <svg class="contact__icon" viewBox="0 0 24 24" fill="none" stroke="#e8101d" stroke-width="1.3"><rect x="3" y="6" width="18" height="14"/><path d="M3 6l9 8 9-8M3 20l7-6M21 20l-7-6"/></svg>
        <span class="contact__text">email</span>
      </li>
      <li class="contact__item" style="top:272px">
        <svg class="contact__icon" viewBox="0 0 24 24" fill="none" stroke="#e8101d" stroke-width="1.2"><circle cx="12" cy="12" r="9"/><ellipse cx="12" cy="12" rx="4" ry="9"/><path d="M3 12h18M5 7h14M5 17h14"/></svg>
        <span class="contact__text">website</span>
      </li>
      <li class="contact__item" style="top:308px">
        <svg class="contact__icon" viewBox="0 0 24 24"><path fill="#e8101d" d="M16 2a5 5 0 0 0-5 5c0 4 5 9 5 9s5-5 5-9a5 5 0 0 0-5-5zm0 3a2 2 0 1 1 0 4 2 2 0 0 1 0-4zM2 17h8l1 2H4l-1 3h18l-1-3h-3l1-2h3l2 5H1z"/></svg>
        <span class="contact__text">Address</span>
      </li>
    </ul>
  </section>
</div>
</body>
</html>
```